Coastline Premier Retreats Business Card Design

Design a business card for Coastline Premier Retreats. Look at the website for colors and reference. Card should have logo, name, title, office number, mobile number, email, URL and a tagline like, "Luxury Hotel & Resort Email Marketing" (This might change).

https://www.coastlinepremierretreats.example

The rest I will leave up to your imagination.

Contact Information for Business Card

Logo, name, title, office number, mobile number, email, URL and a tagline like, "Luxury Hotel & Resort Email Marketing" (This might change).

```html
<!DOCTYPE html>
<html lang="en">
<head>
<meta charset="utf-8">
<title>Coastline Premier Retreats – Business Card</title>
<link rel="stylesheet" href="https://fonts.googleapis.com/css2?family=Arimo:wght@400;700&display=swap">
<style>
  :root {
    --bg: #e4e4e4;
    --ink: #1b1b1b;
    --paper: #ffffff;
    --accent: #f07320;
    --text: #1e1e1e;
  }
  * { box-sizing: border-box; margin: 0; padding: 0; }
  html, body { width: 1200px; height: 998px; overflow: hidden; }
  body {
    background: var(--bg);
    font-family: "Arimo", Arial, sans-serif;
    position: relative;
  }
  .card {
    position: absolute;
    width: 620px;
    height: 354px;
    border-radius: 3px;
    overflow: hidden;
    box-shadow: 0 6px 18px rgba(0,0,0,0.18);
  }
  .card--front { left: 60px; top: 60px; background: var(--ink); }
  .card--back { left: 520px; top: 570px; background: var(--paper); }

  .brand {
    display: flex;
    align-items: center;
    gap: 12px;
    font-weight: 700;
    text-transform: uppercase;
    letter-spacing: 0.04em;
    white-space: nowrap;
  }
  .brand__square { background: var(--accent); flex: none; }
  .card--front .brand {
    position: absolute; inset: 0;
    justify-content: center;
    color: var(--paper);
    font-size: 28px;
  }
  .card--front .brand__square { width: 20px; height: 20px; }

  .card--back .wave { position: absolute; inset: 0; width: 100%; height: 100%; }
  .card--back .brand {
    position: absolute; left: 28px; top: 112px;
    color: var(--ink);
    font-size: 14px;
    gap: 9px;
  }
  .card--back .brand__square { width: 13px; height: 13px; }

  .details {
    position: absolute; left: 320px; top: 18px;
    padding-left: 16px;
    border-left: 2px solid var(--accent);
    color: var(--text);
    font-size: 13px;
    line-height: 1.3;
  }
  .details__name {
    color: var(--accent);
    font-weight: 700;
    font-size: 20px;
    text-transform: uppercase;
    letter-spacing: 0.02em;
  }
  .details__title { margin-top: 1px; }
  .details__tagline { margin-bottom: 6px; }
  .contact { list-style: none; }
  .contact li { display: flex; align-items: center; gap: 7px; height: 20px; white-space: nowrap; }
  .contact svg { width: 12px; height: 12px; fill: var(--accent); flex: none; }
</style>
</head>
<body>

<section class="card card--front" aria-label="Business card front">
  <div class="brand"><span class="brand__square"></span>Coastline Premier Retreats</div>
</section>

<section class="card card--back" aria-label="Business card back">
  <svg class="wave" viewBox="0 0 620 354" preserveAspectRatio="none" aria-hidden="true">
    <path d="M0,330 C170,330 260,300 350,268 C440,236 530,226 620,222 L620,354 L0,354 Z" fill="var(--ink)"/>
    <path d="M50,316 C190,312 270,285 350,254 C440,222 525,213 610,210" fill="none" stroke="var(--accent)" stroke-width="6" stroke-linecap="round"/>
  </svg>

  <div class="brand"><span class="brand__square"></span>Coastline Premier Retreats</div>

  <div class="details">
    <p class="details__name">Daniel Marlowe</p>
    <p class="details__title">Co-Founder</p>
    <p class="details__tagline">Luxury Hotel &amp; Resort<br>Email Marketing</p>
    <ul class="contact">
      <li><svg viewBox="0 0 16 16"><path d="M3 2h3l1.5 3.5-2 1.3a8 8 0 0 0 3.7 3.7l1.3-2L14 10v3a1 1 0 0 1-1 1C7 14 2 9 2 3a1 1 0 0 1 1-1z"/></svg>555-210-4637</li>
      <li><svg viewBox="0 0 16 16"><path d="M5 1h6a1 1 0 0 1 1 1v12a1 1 0 0 1-1 1H5a1 1 0 0 1-1-1V2a1 1 0 0 1 1-1zm0.5 1.5v9.5h5V2.5zM8 12.6a.7.7 0 1 0 0 1.4.7.7 0 0 0 0-1.4z"/></svg>555-318-9052</li>
      <li><svg viewBox="0 0 16 16"><path d="M1 3h14v10H1zm1.5 1.3V12h11V4.3L8 8.6z"/><path d="M2 3.5l6 4.7 6-4.7" fill="none" stroke="#fff" stroke-width="0.8"/></svg>info@coastlinepremierretreats.example</li>
      <li><svg viewBox="0 0 16 16"><circle cx="8" cy="8" r="7"/><path d="M1.5 8h13M8 1.2c-2.5 2-2.5 11.6 0 13.6M8 1.2c2.5 2 2.5 11.6 0 13.6" fill="none" stroke="#fff" stroke-width="0.9"/></svg>www.coastlinepremierretreats.example</li>
    </ul>
  </div>
</section>

</body>
</html>
```